Before the kettle boils, pocast with content in its majority of technology

Page dedicated to a pocast with content in its majority of technology. The page also contains the chapters of the podcast (pluggin vocalink) will also contain news. Preferably Worpress. There is already a very basic page with a simple theme, the logo and little more, I would like something more professional. Www.lamparadebolsillo.com The logo does not want to change.

Target Market(s)

Anyone

Colors

Designer to choose colors to be used in the design.

Requirements
Must have
• You can put the vocalink pluggin with the podcast chapters

```html
<!DOCTYPE html>
<html lang="es">
<head>
<meta charset="utf-8">
<title>Before the kettle boils – Podcast de Tecnología</title>
<link href="https://fonts.googleapis.com/css2?family=Oswald:wght@400;500;600;700&family=Open+Sans:wght@400;600;700&display=swap" rel="stylesheet">
<style>
:root{
  --orange:#f47b20;
  --orange-dark:#e06a10;
  --ink:#222222;
  --text:#555555;
  --muted:#8a8a8a;
  --line:#e3e3e3;
  --card-border:#dedede;
  --footer:#1d1d1d;
  --footer-line:#333333;
  --white:#ffffff;
  --wave:#2b2b2b;
}
*{box-sizing:border-box;margin:0;padding:0}
html,body{width:1200px;height:3673px;overflow:hidden}
body{background:var(--white);font-family:"Open Sans",Arial,sans-serif;color:var(--text);position:relative}
.oswald{font-family:"Oswald",Arial,sans-serif}

/* Header / hero */
.hero{position:absolute;left:0;top:0;width:1200px;height:558px;
  background:linear-gradient(100deg,#2b2421 0%,#4a3a30 30%,#6b5646 55%,#3a302a 80%,#1f1a18 100%)}
.hero-photo{position:absolute;inset:0;
  background:radial-gradient(ellipse 260px 320px at 880px 300px,rgba(190,160,140,.55),transparent 70%),
             linear-gradient(180deg,rgba(0,0,0,.15),rgba(0,0,0,.35))}
.logo{position:absolute;left:130px;top:20px;display:flex;flex-direction:column;align-items:center;gap:6px}
.logo-mark{width:52px;height:52px;border-radius:50%;background:var(--orange)}
.logo-name{font-family:"Oswald",Arial,sans-serif;font-weight:500;font-size:15px;color:var(--white);text-transform:uppercase;letter-spacing:.5px}
.nav{position:absolute;top:46px;left:343px;display:flex;align-items:center;gap:26px}
.nav a{font-family:"Oswald",Arial,sans-serif;font-size:15px;font-weight:500;color:var(--white);text-decoration:none;text-transform:uppercase}
.nav a.active{color:var(--orange)}
.nav-actions{position:absolute;top:38px;left:884px;display:flex;gap:8px}
.pill-btn{height:38px;padding:0 18px;border-radius:19px;display:flex;align-items:center;gap:6px;font-family:"Oswald",Arial,sans-serif;font-size:14px;font-weight:500;color:var(--white);text-transform:uppercase}
.pill-btn.login{border:2px solid var(--white)}
.pill-btn.signup{background:var(--orange)}
.hero-title{position:absolute;left:98px;top:216px;font-family:"Oswald",Arial,sans-serif;font-weight:600;font-size:40px;color:var(--white);text-transform:uppercase;letter-spacing:.5px}
.hero-text{position:absolute;left:98px;top:286px;width:520px;font-size:18px;line-height:28px;color:var(--white);font-weight:600}
.hero-btn{position:absolute;left:98px;top:366px;width:168px;height:44px;border:2px solid var(--white);border-radius:22px;display:flex;align-items:center;justify-content:center;font-family:"Oswald",Arial,sans-serif;font-size:16px;color:var(--white);text-transform:uppercase}
.hero-dots{position:absolute;left:564px;top:488px;display:flex;gap:8px}
.hero-dots span{width:12px;height:12px;border-radius:50%;border:2px solid var(--white)}
.hero-dots span.on{background:var(--white)}

/* Main column */
.section-title{position:absolute;left:98px;top:624px;font-family:"Oswald",Arial,sans-serif;font-weight:600;font-size:24px;color:var(--ink);text-transform:uppercase}
.episode{position:absolute;left:98px;width:624px;border:1px solid var(--card-border);background:var(--white);padding:22px 20px 0 20px;box-shadow:0 1px 3px rgba(0,0,0,.06)}
.episode h2{font-family:"Oswald",Arial,sans-serif;font-weight:500;font-size:22px;color:var(--ink);text-transform:uppercase;line-height:30px}
.meta{display:flex;align-items:center;gap:10px;margin-top:10px;font-size:12px;color:var(--muted)}
.meta .sep{color:#bbb}
.meta svg{vertical-align:-2px}
.stars{color:var(--orange);letter-spacing:1px;font-size:13px}
.episode-photo{margin-top:14px;height:250px;width:100%}
.player{margin-top:14px;position:relative;height:62px}
.player-label{display:flex;align-items:center;gap:8px;font-size:10px;color:#444;text-transform:uppercase}
.play{width:15px;height:15px;border-radius:50%;background:var(--orange);position:relative}
.play::after{content:"";position:absolute;left:6px;top:4px;border-left:5px solid var(--white);border-top:3.5px solid transparent;border-bottom:3.5px solid transparent}
.player-tag{position:absolute;right:10px;top:4px;width:34px;height:10px;border-radius:5px;background:#cfcfcf}
.wave{position:absolute;left:0;right:40px;top:28px;height:30px;
  background:repeating-linear-gradient(90deg,var(--wave) 0 2px,transparent 2px 3px);
  -webkit-mask:linear-gradient(180deg,transparent 0,#000 20%,#000 80%,transparent 100%);
          mask:linear-gradient(180deg,transparent 0,#000 20%,#000 80%,transparent 100%)}
.wave.played{background:linear-gradient(90deg,transparent 0,transparent 0),repeating-linear-gradient(90deg,var(--wave) 0 2px,transparent 2px 3px)}
.wave-progress{position:absolute;left:0;top:28px;height:30px;width:75%;
  background:repeating-linear-gradient(90deg,var(--orange) 0 2px,transparent 2px 3px);
  -webkit-mask:linear-gradient(180deg,transparent 0,#000 20%,#000 80%,transparent 100%);
          mask:linear-gradient(180deg,transparent 0,#000 20%,#000 80%,transparent 100%)}
.excerpt{margin-top:16px;font-size:12.5px;line-height:24px;color:var(--text)}
.card-foot{position:absolute;left:20px;right:20px;bottom:20px;display:flex;justify-content:space-between;align-items:center}
.read-more{height:32px;padding:0 22px;border:1px solid #cfcfcf;border-radius:16px;display:flex;align-items:center;font-size:12px;font-weight:600;color:var(--orange);text-transform:uppercase}
.shares{display:flex;gap:6px}
.share{display:flex;align-items:center;height:20px;font-size:10px;color:#333}
.share b{height:20px;padding:0 7px;display:flex;align-items:center;background:#eef1f6;border:1px solid #c8cfdc;border-radius:3px;font-weight:600}
.share span{height:20px;padding:0 6px;display:flex;align-items:center;border:1px solid #d5d5d5;border-left:none;border-radius:0 3px 3px 0;background:var(--white)}
.view-more{position:absolute;font-size:13px;font-weight:700;color:var(--orange);text-transform:uppercase}

/* Sidebar */
.ad{position:absolute;left:756px;top:628px;width:343px;height:236px;border:4px solid #eee;
  background:linear-gradient(135deg,#6d5a52 0%,#a58b7c 40%,#4a3e3a 100%)}
.ad-label{position:absolute;left:0;top:114px;width:320px;padding:10px 8px;background:rgba(30,30,30,.72);border:2px solid var(--white);border-left:none}
.ad-label strong{display:block;font-family:"Oswald",Arial,sans-serif;font-size:22px;color:var(--white);text-transform:uppercase;font-weight:500;border-bottom:2px solid var(--white);padding-bottom:4px}
.ad-label em{display:block;font-style:normal;font-family:"Oswald",Arial,sans-serif;font-size:15px;color:var(--white);text-transform:uppercase;letter-spacing:1.5px;padding-top:4px}
.widget-head{position:absolute;left:756px;width:343px;height:42px;border-bottom:3px solid var(--orange)}
.widget-head span{position:absolute;left:0;top:0;height:42px;padding:0 36px 0 12px;background:var(--orange);display:flex;align-items:center;font-family:"Oswald",Arial,sans-serif;font-weight:500;font-size:19px;color:var(--white);text-transform:uppercase;clip-path:polygon(0 0,calc(100% - 22px) 0,100% 100%,0 100%)}
.recent{position:absolute;left:756px;top:1004px;width:343px}
.recent-item{display:flex;gap:12px;height:106px}
.recent-thumb{width:108px;height:78px;flex:none;position:relative;border:1px solid #ddd}
.recent-thumb::after{content:"";position:absolute;right:-10px;top:29px;width:20px;height:20px;border-radius:50%;background:var(--orange)}
.recent-title{font-family:"Oswald",Arial,sans-serif;font-size:17px;line-height:25px;color:var(--ink);padding-top:6px}
.recent-meta{font-size:10px;color:var(--muted);margin-top:4px}
.sidebar-rule{position:absolute;left:756px;width:343px;border-top:1px solid var(--line)}
.newsletter{position:absolute;left:756px;top:1680px;width:343px;height:202px;border:1px solid var(--card-border);padding:18px 16px}
.news-input{height:40px;border:1px solid #d0d0d0;border-radius:20px;display:flex;align-items:center;padding-left:18px;font-size:10px;color:#777;text-transform:uppercase}
.news-btn{margin-top:12px;height:40px;border:1px solid #cfcfcf;border-radius:20px;display:flex;align-items:center;justify-content:center;font-family:"Oswald",Arial,sans-serif;font-size:16px;color:var(--orange);text-transform:uppercase}
.news-note{margin-top:12px;font-size:10.5px;line-height:17px;color:#666}
.community{position:absolute;left:756px;top:2008px;width:343px;height:272px;border:1px solid var(--card-border);padding:8px}
.community-cover{height:146px;position:relative;background:linear-gradient(120deg,#5a5f6a,#8f8b86 50%,#3e3a38)}
.community-badge{position:absolute;left:10px;top:10px;width:70px;height:70px;background:#2c2c2c;border:2px solid var(--white)}
.community-name{position:absolute;left:92px;top:14px;font-family:"Oswald",Arial,sans-serif;font-size:15px;color:var(--white);text-transform:uppercase}
.community-btn{position:absolute;bottom:10px;height:26px;padding:0 10px;display:flex;align-items:center;background:#f4f4f4;border:1px solid #ccc;border-radius:3px;font-size:11px;font-weight:600;color:#333}
.community-note{margin-top:14px;font-size:11px;color:#666}
.faces{display:flex;gap:4px;margin-top:12px}
.faces span{width:44px;height:44px;background:linear-gradient(135deg,#a89a90,#5e5650)}
.poster{position:absolute;left:756px;top:2354px;width:343px;height:476px;border:4px solid #eee;
  background:linear-gradient(180deg,#1b2a44 0%,#37557a 40%,#9a9fa8 70%,#2a3342 100%)}

/* Footer */
.footer{position:absolute;left:0;top:3436px;width:1200px;height:237px;background:var(--footer);border-top:4px solid var(--orange)}
.contact-row{position:absolute;top:46px;left:0;width:1200px;display:flex;justify-content:center;gap:62px}
.contact{display:flex;align-items:center;gap:14px;font-size:13px;line-height:20px;color:#ddd}
.contact-icon{width:44px;height:44px;border-radius:50%;border:1px solid #888;display:flex;align-items:center;justify-content:center}
.footer-links{position:absolute;top:116px;width:1200px;text-align:center;font-size:14px;color:#ddd;word-spacing:2px}
.footer-bar{position:absolute;top:158px;left:98px;width:1004px;border-top:1px solid var(--footer-line)}
.copyright{position:absolute;left:98px;top:196px;font-size:12px;color:#ccc}
.social{position:absolute;right:98px;top:188px;display:flex;gap:8px}
.social span{width:32px;height:32px;border-radius:50%;border:1px solid #999}
</style>
</head>
<body>

<header class="hero">
  <div class="hero-photo" role="img" aria-label="Joven con auriculares bailando al ritmo de la música en una calle"></div>
  <div class="logo">
    <span class="logo-mark"></span>
    <span class="logo-name">Before the kettle boils</span>
  </div>
  <nav class="nav">
    <a class="active">Home</a><a>Podcasts</a><a>Features</a><a>Pricing</a><a>Program</a><a>Contact</a>
    <svg width="16" height="16" viewBox="0 0 16 16"><circle cx="6.5" cy="6.5" r="5" fill="none" stroke="#fff" stroke-width="2"/><line x1="10" y1="10" x2="15" y2="15" stroke="#fff" stroke-width="2"/></svg>
  </nav>
  <div class="nav-actions">
    <span class="pill-btn login"><svg width="10" height="12" viewBox="0 0 10 12"><rect x="0" y="5" width="10" height="7" fill="#fff"/><path d="M2 5V3.5a3 3 0 0 1 6 0V5" fill="none" stroke="#fff" stroke-width="1.6"/></svg>Login</span>
    <span class="pill-btn signup"><svg width="11" height="11" viewBox="0 0 11 11"><path d="M1 10l1-3 6-6 2 2-6 6z" fill="#fff"/></svg>Sign up</span>
  </div>
  <h1 class="hero-title">Podcast de Techologia</h1>
  <p class="hero-text">Nam libero tempore, cum soluta nobis est eligendi otio cumque nihil impedit quo minus.</p>
  <span class="hero-btn">Start now!</span>
  <div class="hero-dots"><span class="on"></span><span></span><span></span><span></span></div>
</header>

<h2 class="section-title">Latest Podcast</h2>

<article class="episode" style="top:686px;height:650px">
  <h2>Cambio de logo</h2>
  <div class="meta">
    <svg width="11" height="11" viewBox="0 0 11 11"><rect x="0" y="1" width="11" height="10" fill="#f47b20"/></svg>19 May, 2017 <span class="sep">|</span>
    <svg width="10" height="11" viewBox="0 0 10 11"><circle cx="5" cy="3" r="3" fill="#f47b20"/><path d="M0 11a5 5 0 0 1 10 0z" fill="#f47b20"/></svg>de marlow <span class="sep">|</span>
    <span class="stars">★★★★☆</span>(34 Reviews)
  </div>
  <div class="episode-photo" role="img" aria-label="Persona con los brazos en alto frente a un atardecer dorado" style="background:linear-gradient(180deg,#f6c35a 0%,#f0a53a 45%,#c98a3a 75%,#8a6a48 100%)"></div>
  <div class="player">
    <div class="player-label"><span class="play"></span>Change logo</div>
    <span class="player-tag"></span>
    <div class="wave"></div><div class="wave-progress"></div>
  </div>
  <p class="excerpt">Hello to Tod @ s!<br>Is it obvious, then? We renew the design of the logo and something on the web. Here the changes will go little by little but I will try to leave everything that I want to modify done in a week at most, everything will depend on the time that I can dedicate to him although the difficult thing is already done.</p>
  <div class="card-foot">
    <span class="read-more">Read more &gt;&gt;</span>
    <div class="shares"><span class="share"><b>Like</b><span>200</span></span><span class="share"><b>Share</b><span>200</span></span><span class="share"><b>+1</b><span>200</span></span></div>
  </div>
</article>

<article class="episode" style="top:1354px;height:648px">
  <h2>Do you like series? Do you know reelnest.tv?</h2>
  <div class="meta">
    <svg width="11" height="11" viewBox="0 0 11 11"><rect x="0" y="1" width="11" height="10" fill="#f47b20"/></svg>17 May, 2017 <span class="sep">|</span>
    <svg width="10" height="11" viewBox="0 0 10 11"><circle cx="5" cy="3" r="3" fill="#f47b20"/><path d="M0 11a5 5 0 0 1 10 0z" fill="#f47b20"/></svg>de marlow <span class="sep">|</span>
    <span class="stars">★★★★☆</span>(34 Reviews)
  </div>
  <div class="episode-photo" role="img" aria-label="Auriculares amarillos y un teléfono sobre una mesa de madera" style="background:linear-gradient(90deg,#8a5a34 0%,#b07a48 35%,#3a3a3a 60%,#a8703e 100%)"></div>
  <div class="player">
    <div class="player-label"><span class="play"></span>Do you like series? Do you know reelnest.tv?</div>
    <span class="player-tag"></span>
    <div class="wave"></div>
  </div>
  <p class="excerpt">Hello everyone!<br>Today chapter dedicated to the lovers of the series and the films. It is the streaming video service of the website reelnest.tv portal dedicated to learning English through the method of watching movies and series in English with subtitles.</p>
  <div class="card-foot">
    <span class="read-more">Read more &gt;&gt;</span>
    <div class="shares"><span class="share"><b>Like</b><span>200</span></span><span class="share"><b>Share</b><span>200</span></span><span class="share"><b>+1</b><span>200</span></span></div>
  </div>
</article>

<article class="episode" style="top:2022px;height:648px">
  <h2>An advertisement and a test</h2>
  <div class="meta">
    <svg width="11" height="11" viewBox="0 0 11 11"><rect x="0" y="1" width="11" height="10" fill="#f47b20"/></svg>May 13, 2017 <span class="sep">|</span>
    <svg width="10" height="11" viewBox="0 0 10 11"><circle cx="5" cy="3" r="3" fill="#f47b20"/><path d="M0 11a5 5 0 0 1 10 0z" fill="#f47b20"/></svg>de marlow <span class="sep">|</span>
    <span class="stars">★★★★☆</span>(34 Reviews)
  </div>
  <div class="episode-photo" role="img" aria-label="Mujer con auriculares disfrutando de la música" style="background:linear-gradient(110deg,#2a2a4a 0%,#5a4a6a 35%,#c89a7a 60%,#3a2f4a 100%)"></div>
  <div class="player">
    <div class="player-label"><span class="play"></span>An advertisement and a test</div>
    <span class="player-tag"></span>
    <div class="wave"></div>
  </div>
  <p class="excerpt">Hello everyone!<br>Yes, I know it has happened again, a long time since the last publication. This I have very abandoned and there is no excuse, I feel sorry but it is true, for ganduleria or for reasons of time I have not dedicated the attention that deserves.</p>
  <div class="card-foot">
    <span class="read-more">Read more &gt;&gt;</span>
    <div class="shares"><span class="share"><b>Like</b><span>200</span></span><span class="share"><b>Share</b><span>200</span></span><span class="share"><b>+1</b><span>200</span></span></div>
  </div>
</article>

<article class="episode" style="top:2690px;height:634px">
  <h2>Security in your mail</h2>
  <div class="meta">
    <svg width="11" height="11" viewBox="0 0 11 11"><rect x="0" y="1" width="11" height="10" fill="#f47b20"/></svg>Nov 23, 2016 <span class="sep">|</span>
    <svg width="10" height="11" viewBox="0 0 10 11"><circle cx="5" cy="3" r="3" fill="#f47b20"/><path d="M0 11a5 5 0 0 1 10 0z" fill="#f47b20"/></svg>de marlow <span class="sep">|</span>
    <span class="stars">★★★★☆</span>(34 Reviews)
  </div>
  <div class="episode-photo" role="img" aria-label="Auriculares negros en primer plano sobre fondo claro" style="background:linear-gradient(120deg,#d8dee2 0%,#9aa6ac 30%,#2a3034 60%,#5e6a70 100%)"></div>
  <div class="player">
    <div class="player-label"><span class="play"></span>Security in your mail</div>
    <span class="player-tag"></span>
    <div class="wave"></div>
  </div>
  <p class="excerpt">Hello everyone!<br>Today little more to say about here said in the podcast. For those who need an extra point of security in the email is SealPost. Free and paid plans, coding, messages that can be destroyed, etc.</p>
  <div class="card-foot">
    <span class="read-more">Read more &gt;&gt;</span>
    <div class="shares"><span class="share"><b>Like</b><span>200</span></span><span class="share"><b>Share</b><span>200</span></span><span class="share"><b>+1</b><span>200</span></span></div>
  </div>
</article>

<span class="view-more" style="left:98px;top:3356px">View more &gt;&gt;</span>

<!-- Sidebar -->
<aside>
  <div class="ad" role="img" aria-label="Micrófono de estudio en primer plano, anuncio de publicidad en podcast">
    <div class="ad-label"><strong>Podcast advertising</strong><em>What you need to know</em></div>
  </div>

  <div class="widget-head" style="top:938px"><span>Recent posts</span></div>
  <div class="recent">
    <div class="recent-item"><div class="recent-thumb" role="img" aria-label="Teléfono en una mano" style="background:linear-gradient(135deg,#3a3a3a,#8a8a8a)"></div><div><div class="recent-title">Un anuncio y una prueba</div><div class="recent-meta">▪ 13 May, 2017 &nbsp;|&nbsp; ▪ marlow</div></div></div>
    <div class="recent-item"><div class="recent-thumb" role="img" aria-label="Paisaje nevado" style="background:linear-gradient(135deg,#9fb8c4,#e6eef0)"></div><div><div class="recent-title">¿Te gustan las series?¿Conoces reelnest.tv?</div><div class="recent-meta">▪ 13 May, 2017 &nbsp;|&nbsp; ▪ marlow</div></div></div>
    <div class="recent-item"><div class="recent-thumb" role="img" aria-label="Ilustración de seguridad" style="background:linear-gradient(135deg,#6a8a9a,#c8d4da)"></div><div><div class="recent-title">Seguridad en tu Mail</div><div class="recent-meta">▪ 13 May, 2017 &nbsp;|&nbsp; ▪ marlow</div></div></div>
    <div class="recent-item"><div class="recent-thumb" role="img" aria-label="Persona escuchando música" style="background:linear-gradient(135deg,#4a3a4a,#b090a0)"></div><div><div class="recent-title">Kumo Pad 2, calidad precio insuperable</div><div class="recent-meta">▪ 13 May, 2017 &nbsp;|&nbsp; ▪ marlow</div></div></div>
    <div class="recent-item"><div class="recent-thumb" role="img" aria-label="Cielo al atardecer" style="background:linear-gradient(135deg,#c89a6a,#5a6a7a)"></div><div><div class="recent-title">Tertulia Pomeliana : Servicios en la nube &nbsp;(Podcast)</div><div class="recent-meta">▪ 13 May, 2017 &nbsp;|&nbsp; ▪ marlow</div></div></div>
  </div>
  <span class="view-more" style="left:756px;top:1538px;font-size:11px">View more &gt;&gt;</span>
  <div class="sidebar-rule" style="top:1584px"></div>

  <div class="widget-head" style="top:1620px"><span>Newsletter sign up</span></div>
  <div class="newsletter">
    <div class="news-input">Enter your email address</div>
    <div class="news-btn">Sign up</div>
    <p class="news-note">By signing up, you are opting in to receive periodic communications from Before the kettle boils</p>
  </div>
  <div class="sidebar-rule" style="top:1912px"></div>

  <div class="widget-head" style="top:1950px"><span>Join us on Circlebook</span></div>
  <div class="community">
    <div class="community-cover" role="img" aria-label="Portada de la comunidad con un paisaje">
      <span class="community-badge"></span>
      <span class="community-name">Before the kettle boils</span>
      <span class="community-btn" style="left:92px">Like Page</span>
      <span class="community-btn" style="right:10px">Sign Up</span>
    </div>
    <p class="community-note">Be the first of your friends to like this</p>
    <div class="faces"><span></span><span></span><span></span><span></span><span></span><span></span></div>
  </div>
  <div class="sidebar-rule" style="top:2312px"></div>

  <div class="poster" role="img" aria-label="Cartel de película nocturna con un espejo retrovisor y una figura en la carretera"></div>
</aside>

<footer class="footer">
  <div class="contact-row">
    <div class="contact"><span class="contact-icon"><svg width="14" height="18" viewBox="0 0 14 18"><path d="M7 0a7 7 0 0 0-7 7c0 5 7 11 7 11s7-6 7-11a7 7 0 0 0-7-7z" fill="#ddd"/><circle cx="7" cy="7" r="2.5" fill="#1d1d1d"/></svg></span><span>118 Larkspur Lane, 4th Floor<br>Brookhaven, BH 20417</span></div>
    <div class="contact"><span class="contact-icon"><svg width="16" height="16" viewBox="0 0 16 16"><path d="M3 1l3 3-2 2a10 10 0 0 0 6 6l2-2 3 3-2 2C6 15 1 10 1 3z" fill="#ddd"/></svg></span><span>+1 555 014 2290</span></div>
    <div class="contact"><span class="contact-icon"><svg width="18" height="13" viewBox="0 0 18 13"><rect x="0" y="0" width="18" height="13" fill="#ddd"/><path d="M0 0l9 7 9-7" fill="none" stroke="#1d1d1d" stroke-width="1.5"/></svg></span><span>info@beforethekettleboils.com</span></div>
  </div>
  <div class="footer-links">Home &nbsp;|&nbsp; Podcasts &nbsp;|&nbsp; Features &nbsp;|&nbsp; Pricing &nbsp;|&nbsp; Program &nbsp;|&nbsp; Contact</div>
  <div class="footer-bar"></div>
  <p class="copyright">Copyrights © 2017, Before the kettle boils . All rights reserved.</p>
  <div class="social"><span></span><span></span><span></span><span></span></div>
</footer>

</body>
</html>
```